Podcast Cover Art for rebranded podcast - I have inspiration for the designs

I've had a podcast ("Paperboat Radio Hour") since 2018, but I'm in the process of rebranding it. I've attached the old cover art below, which I loved, but I don't need it to look like that at all. The rebranded podcast is called 'Open Window with Marnie Cole.' I've included the show description at the bottom. I've been working on various design options in Canva, but not obsessed with anything yet, but I'm attaching the ones I do like that I think just need some refining. My very favorite is the one labeled 'favorite_Open Window' so I wouldn't mind keeping that general idea but perfected by a designer. Ultimately, I want something cool, fairly clean, modern, eye catching. I'm into neutrals with maybe a pop of color, so think black, white, grey..maybe silver, and I love a pop of red..and I'm not opposed to other options for the pop color. The show is going to be inspiring, entertaining, and funny. Oh and one other idea I had but I'm not sure if it makes sense with the title and/or what the show is about..but a vinyl record with Open Window with Marnie Cole on it somehow, on a record player..not sure.

Ever wonder what it means to truly live authentically? Curious about how to embrace the unpredictability of life? Ready for some heartfelt and lighthearted conversations that inspire and entertain?
Join Marnie Cole as she dives into the raw, real, and unscripted moments of life. In each episode, Marnie brings candid conversations and genuine insights into the ups and downs we all experience. From personal growth and self-discovery to inspiring stories and valuable life lessons, "Open Window" is a space where authenticity reigns and spontaneity is celebrated.
Whether she's sharing her own journey or chatting with inspiring guests, Marnie invites you to explore the beauty of living life without a script. Expect honest reflections, thought-provoking discussions, and a refreshing perspective on navigating life's unpredictable path—all with a dash of fun and humor to keep things lively and entertaining. Step into the unscripted moments of life and tune in for a blend of depth and lightheartedness that will leave you inspired, smiling, and most importantly laughing.

Target Market(s)

25-50 year old women and men (primarily women)

Font styles to use
Sans Serif

Requirements
Should not have
• nothing too feminine or girly, nothing cheesy :)

```html
<!DOCTYPE html>
<html lang="en">
<head>
<meta charset="utf-8">
<title>Open Window with Marnie Cole — Podcast Cover</title>
<link rel="stylesheet" href="https://fonts.googleapis.com/css2?family=Anton&family=Montserrat:wght@400;800&family=Mr+Dafoe&display=swap">
<style>
  :root {
    --sky-top: #4f77ad;
    --sky-low: #8eaacb;
    --sea-deep: #1d6a80;
    --sea-green: #2f8a7c;
    --foam: #eef2ee;
    --shallows: #c7dbd2;
    --sand: #e8e2d2;
    --white: #ffffff;
    --red: #e8002a;
    --ink: #1c1c1c;
  }
  * { margin: 0; padding: 0; box-sizing: border-box; }
  html, body { width: 1200px; height: 1200px; overflow: hidden; background: var(--sand); }
  .cover { position: relative; width: 1200px; height: 1200px; overflow: hidden; }
  .cover__scene { position: absolute; inset: 0; width: 100%; height: 100%; }

  .title { position: absolute; left: 0; right: 0; top: 118px; text-align: center; }
  .title__top {
    display: flex; align-items: center; justify-content: center; gap: 26px;
    font-family: "Montserrat", sans-serif; font-weight: 800;
    font-size: 166px; line-height: 1; color: var(--white); letter-spacing: -2px;
  }
  .title__rule { width: 200px; height: 2px; background: var(--white); }
  .title__main {
    margin-top: 22px;
    font-family: "Anton", sans-serif; font-size: 246px; line-height: 1;
    color: var(--red); letter-spacing: 2px;
  }

  .host { position: absolute; left: 96px; top: 726px; }
  .host__with {
    font-family: "Mr Dafoe", cursive; font-size: 108px; line-height: 1;
    color: var(--ink); transform: translateX(4px);
  }
  .host__portrait { position: absolute; left: -6px; top: 122px; width: 238px; height: 238px; }
  .host__name {
    position: absolute; left: 256px; top: 128px; white-space: nowrap;
    font-family: "Montserrat", sans-serif; line-height: 1;
  }
  .host__first { display: block; font-weight: 800; font-size: 120px; color: var(--red); letter-spacing: -1px; }
  .host__last { display: block; font-weight: 400; font-size: 116px; color: var(--ink); margin-top: 8px; }
</style>
</head>
<body>
<main class="cover">
  <svg class="cover__scene" viewBox="0 0 1200 1200" role="img" aria-label="Photograph of a woman in a straw hat and green palm-print dress holding a glass, walking on a white sand beach toward turquoise surf under a blue sky">
    <defs>
      <linearGradient id="scene" x1="0" y1="0" x2="0" y2="1">
        <stop offset="0" stop-color="var(--sky-top)"/>
        <stop offset="0.27" stop-color="var(--sky-low)"/>
        <stop offset="0.29" stop-color="var(--sea-deep)"/>
        <stop offset="0.40" stop-color="var(--sea-green)"/>
        <stop offset="0.46" stop-color="var(--foam)"/>
        <stop offset="0.62" stop-color="var(--shallows)"/>
        <stop offset="0.72" stop-color="var(--sand)"/>
        <stop offset="1" stop-color="var(--sand)"/>
      </linearGradient>
    </defs>
    <rect width="1200" height="1200" fill="url(#scene)"/>
  </svg>

  <header class="title">
    <div class="title__top">
      <span class="title__rule"></span>
      <span>OPEN</span>
      <span class="title__rule"></span>
    </div>
    <h1 class="title__main">WINDOW</h1>
  </header>

  <section class="host">
    <div class="host__with">With</div>
    <svg class="host__portrait" viewBox="0 0 238 238" role="img" aria-label="Circular portrait photo of host Marnie Cole">
      <defs>
        <radialGradient id="portrait" cx="0.5" cy="0.4" r="0.6">
          <stop offset="0" stop-color="#7a6a5c"/>
          <stop offset="0.6" stop-color="#3e4a3a"/>
          <stop offset="1" stop-color="#2a3326"/>
        </radialGradient>
      </defs>
      <circle cx="119" cy="119" r="119" fill="url(#portrait)"/>
    </svg>
    <p class="host__name">
      <span class="host__first">MARNIE</span>
      <span class="host__last">COLE</span>
    </p>
  </section>
</main>
</body>
</html>
```